Design Website to Recruit next Generation of Steel Harbor's Order Vantage

Design a cool website that provides just enough information to be intriguing to teenagers who compete in combat sports. The format is to make this an invite-only team of high-school-aged competitors in combat sports (predominately Jiu Jitsu right now). Cinder Ravens can participate in similar assignments to earn consideration. We are modeled after the Order Vantage formed in Steel Harbor and would like to keep that look and feel. The document attached "OV - Ideas and Content for Website" shows our initial thoughts and here is more about us:

Goal - To promote the success of committed teenage Jiu Jitsu competitors who excel through focused preparation and deliberate practice.

Why - Prove the core principles of success.

How - Success is its own reward and always entails an element of the unknown/uncontrollable. We reward preparation. Setting clear goals (SMART), deliberate practice, building mental models (domain specific knowledge), restorative recovery, nutritional coaching, power of teaching others, sports science (strength & conditioning), expert guidance, personalized development plans, accountability, Quantified Self, gamification and competitive challenges. What - We will win at the highest of levels across the fight world by applying the general principles of success. These lessons will be carried with them to other areas of their lives.

Our primary goal with the website would be to share our company’s mission statement and promote the success of our sponsored athletes.

The only social media account we have currently is Pixtrelle's @ordervantageK7 (recently established). If you want more of an idea for what our online presence should feel like, then I would suggest watching these two scenes from Steel Harbor:

Recruiting: This scene shows the process for joining Order Vantage: https://vidrelo.net/Qk82LmTrA

Order Vantage Assignments: This shows how assignments are handed out for members to accomplish: https://vidrelo.net/Zp41XwNeB

Order Vantage Color Assignment: This is their first large assignment and where the green color comes from: https://vidrelo.net/Hd67VcJuC

It is also worth noting that "less is more" considering the first rule is, "you do not talk about..." That should carry over to our website and social media presence. We want to share just enough to be intriguing to inquiring minds and motivational for members, but no more.

I have uploaded a bunch of content, but just wanted to give you a broader idea. Feel free to design as you see fit...
Updates

Please stay tuned for the "burning smiley face" files. I have purchased a rendering of it so we have a proprietary vector image to use on our site. There will also be files for different versions of the Order Vantage//OV logos for various subcategories. Here is how they are to be applied: Circled = Primary (for main/landing page), Jiu Jitsu = Pyramid, Wrestling = Traditional, Muay Thai = Rolled, and Legacy OV = Original (coming soon).

Target Market(s)

Teenage competitors of combat sports, their parents, and sponsors of those athletes

Industry/Entity Type

Martial Arts & High School Sports

Coding

Coded - Design and coding required

Number of Pages Required

5+ page

Font styles to use
Sans Serif
Other font styles liked:
• See font in "Circled Logo"

Colors
59FF00
82FF00
B8FF75
E3FFCB
F4FFEA
EB3D1F
EC4F4E
F09395
F8D3D4
FCEDEE

Requirements
Must have
• Cool landing page with logo and brief summary of what we do. Page with 8 rules and explanation for earning an invitation. Plus, accomplishments page for memorializing the success of sponsored "Cinder Ravens"
Should not have
• Individual names

```html
<!DOCTYPE html>
<html lang="en">
<head>
<meta charset="utf-8">
<title>Vantage — Order Vantage</title>
<link rel="stylesheet" href="https://fonts.googleapis.com/css2?family=Poppins:wght@400;500;600;700;800&display=swap">
<style>
:root{
  --red:#e01f3d;
  --red-deep:#c4142f;
  --black:#0b0b0b;
  --panel:#1d1d1d;
  --ink:#222;
  --white:#fff;
  --mist:#f3f3f5;
  --line:#d9d9de;
}
*{box-sizing:border-box;margin:0;padding:0}
html,body{width:1200px;height:5059px;overflow:hidden}
body{position:relative;font-family:'Poppins',sans-serif;color:var(--ink);background:var(--white)}
.abs{position:absolute}

/* nav */
.site-nav{left:0;top:0;width:1200px;height:59px;background:var(--black)}
.brand{left:104px;top:14px;color:var(--white);font-weight:800;font-size:27px;letter-spacing:.5px}
.menu{top:22px;color:var(--white);font-weight:700;font-size:15px}

/* hero */
.hero{left:0;top:59px;width:1200px;height:540px;background:radial-gradient(ellipse at 25% 45%,#4a3a32 0%,#1c1614 40%,#070707 75%),#070707}
.hero-title{right:110px;top:196px;text-align:right;color:var(--white);font-weight:800;font-size:58px;line-height:72px;text-transform:uppercase}
.hero-title span{color:var(--red)}

/* why */
.why{left:0;top:599px;width:1200px;height:595px;background:var(--white)}
.why-photo{left:590px;top:599px;width:610px;height:452px;background:radial-gradient(ellipse at 55% 55%,#5a3a30 0%,#2a1d19 35%,#0c0c0c 75%)}
.why-title{left:112px;top:700px;color:var(--white);font-weight:800;font-size:36px;line-height:54px}
.why-copy{left:112px;top:846px;width:440px;color:var(--white);font-size:15px;line-height:30px}

.glove{left:742px;top:1050px;width:114px;height:184px}
.bag{left:1052px;top:1050px;width:110px;height:384px;border-radius:0 0 40px 40px;background:linear-gradient(90deg,#eee,#f6f6f6,#ececec);opacity:.9}

/* pillars */
.pillar-num{top:1305px;width:200px;text-align:center;color:var(--red);font-weight:800;font-size:72px;line-height:84px}
.pillar-disc{top:1380px;width:186px;height:186px;border-radius:50%;background:radial-gradient(circle at 40% 40%,#fff 55%,#ececec 100%);box-shadow:10px 8px 24px rgba(0,0,0,.08)}
.pillar-label{top:1560px;width:200px;text-align:center;color:var(--red);font-weight:700;font-size:23px;line-height:28px}
.pillar-card{top:1660px;width:296px;height:137px;border:2px solid var(--red);background:var(--white);padding:20px 30px;font-size:14.5px;line-height:40px;box-shadow:0 4px 12px rgba(0,0,0,.12)}
.pillar-icon{width:120px;height:120px}

/* rules */
.rules{left:0;top:1901px;width:1200px;height:1670px;background:linear-gradient(160deg,#f7f7f9,#efeff2 50%,#f8f8fa)}
.section-title{left:0;width:1200px;text-align:center;color:var(--red);font-weight:800;font-size:36px}
.rule-bar{left:286px;width:716px;height:72px;background:var(--white);box-shadow:0 4px 10px rgba(0,0,0,.12);padding-left:56px;font-size:16px;line-height:72px}
.rule-disc{width:148px;height:148px;border-radius:50%;background:radial-gradient(circle at 35% 40%,#fff 55%,#e7e7ea 100%);box-shadow:6px 6px 18px rgba(0,0,0,.1)}
.rule-tag{width:148px;text-align:center;color:var(--red);font-weight:800;font-size:36px;line-height:42px}

/* video */
.video{left:110px;top:3787px;width:976px;height:312px;background:radial-gradient(ellipse at 25% 50%,#6a3a2c 0%,#2b1a16 40%,#0d0d0d 80%)}
.play{left:564px;top:3912px;width:60px;height:60px}

/* faq */
.faq{left:0;top:4183px;width:1200px;height:593px;background:radial-gradient(ellipse at 50% 40%,#fbf8f8,#efe8e8 70%)}
.faq-frame{left:208px;top:4356px;width:778px;height:362px;border:2px solid #8a8a8a}
.faq-q{left:236px;width:718px;height:66px;background:var(--white);box-shadow:0 4px 10px rgba(0,0,0,.18);padding-left:60px;font-size:15px;line-height:66px}
.faq-a{left:267px;top:4462px;width:656px;height:144px;border:2px solid var(--red);padding:16px 50px;color:var(--red);font-size:14.5px;line-height:25px}
.faq-a ul{list-style:disc;padding-left:14px}
.chev{width:22px;height:12px}

/* footer */
.footer{left:0;top:4776px;width:1200px;height:283px;background:radial-gradient(ellipse at 80% 40%,#2a2a2a,#111 60%)}
.social{top:4800px;width:24px;height:24px;border-radius:4px;background:var(--white)}
.foot-brand{left:0;top:4850px;width:1200px;text-align:center;color:var(--white);font-weight:800;font-size:54px;letter-spacing:1px}
.foot-link{top:4940px;color:var(--white);font-weight:700;font-size:16px}
.foot-rule{left:100px;top:4998px;width:1000px;height:1px;background:#777}
.copy{left:0;top:5020px;width:1200px;text-align:center;color:var(--white);font-size:13px}
</style>
</head>
<body>

<header>
  <div class="abs site-nav"></div>
  <div class="abs brand">VANTAGE</div>
  <nav>
    <span class="abs menu" style="left:524px">HOME</span>
    <span class="abs menu" style="left:616px">ABOUT US</span>
    <span class="abs menu" style="left:744px">SERVICES</span>
    <span class="abs menu" style="left:876px">FAQ</span>
    <span class="abs menu" style="left:974px">CONTACT US</span>
  </nav>
</header>

<section>
  <div class="abs hero" role="img" aria-label="Hooded fighter with wrapped fists throwing a punch amid sparks and smoke"></div>
  <h1 class="abs hero-title">Rowan built himself<br>an <span>army....</span></h1>
</section>

<section>
  <div class="abs why"></div>
  <div class="abs why-photo" role="img" aria-label="Two boxing gloves meeting in a dark backlit haze"></div>
  <svg class="abs" style="left:0;top:599px" width="1200" height="595" viewBox="0 0 1200 595">
    <polygon points="0,0 722,0 592,595 0,595" fill="#1d1d1d"/>
    <polygon points="658,452 714,452 640,595 584,595" fill="#e01f3d"/>
    <rect x="0" y="578" width="600" height="17" fill="#fff"/>
    <polygon points="0,590 600,590 598,595 0,595" fill="#111" opacity=".25"/>
  </svg>
  <h2 class="abs why-title">WHY WAS ROWAN<br>BUILDING AN ARMY?</h2>
  <p class="abs why-copy">Sed ut perspiciatis unde omnis iste natus error sit voluptatem accusantium doloremque laudantium, totam rem aperiam, eaque ipsa quae ab illo inventore veritatis et quasi architecto beatae vitae dicta sunt explicabo. Nemo enim ipsam voluptatem quia voluptas sit aspernatur aut odit aut fugit, sed quia consequuntur magni</p>
  <div class="abs glove" role="img" aria-label="Pair of red boxing gloves hanging by their laces" style="background:radial-gradient(ellipse at 50% 65%,#e32d2d 0%,#b3161b 45%,rgba(255,255,255,0) 72%)"></div>
  <div class="abs bag" role="img" aria-label="Faint hanging punching bag"></div>
</section>

<section>
  <svg class="abs" style="left:0;top:1380px" width="1200" height="240" viewBox="0 0 1200 240">
    <path d="M360 185 C 470 200, 520 190, 620 150 S 800 60, 930 75" fill="none" stroke="#ececec" stroke-width="12" stroke-linecap="round"/>
  </svg>

  <div class="abs pillar-num" style="left:168px">01</div>
  <div class="abs pillar-disc" style="left:218px"></div>
  <svg class="abs pillar-icon" style="left:206px;top:1410px" viewBox="0 0 120 120" fill="none" stroke="#111" stroke-width="4" stroke-linejoin="round">
    <rect x="6" y="50" width="24" height="30"/><rect x="86" y="86" width="26" height="26" transform="rotate(-30 99 99)"/>
    <rect x="76" y="6" width="26" height="26" transform="rotate(35 89 19)"/>
    <path d="M30 56 L60 40 L82 56 L70 84 L40 80 Z"/><path d="M46 52 L62 66 M56 46 L72 62"/>
  </svg>
  <div class="abs pillar-label" style="left:180px">SPIRIT</div>

  <div class="abs pillar-num" style="left:498px">02</div>
  <div class="abs pillar-disc" style="left:540px"></div>
  <svg class="abs pillar-icon" style="left:530px;top:1410px" viewBox="0 0 120 120" fill="none" stroke="#111" stroke-width="4" stroke-linejoin="round">
    <path d="M20 100 V74 C8 66 8 40 26 32 C44 24 60 34 60 52 V66 H52 V84 H38 V100"/>
    <circle cx="32" cy="52" r="8"/>
    <path d="M82 22 C70 22 64 34 70 44 C74 50 76 54 76 60 H90 C90 54 92 50 96 44 C102 34 94 22 82 22 Z"/><path d="M76 66 H90"/>
    <path d="M82 6 V12 M62 14 L66 18 M102 14 L98 18" /><path d="M62 76 H100 M62 86 H96" stroke-dasharray="4 4"/>
  </svg>
  <div class="abs pillar-label" style="left:502px">TECHICAL/<br>MIND</div>

  <div class="abs pillar-num" style="left:818px">03</div>
  <div class="abs pillar-disc" style="left:860px"></div>
  <svg class="abs pillar-icon" style="left:860px;top:1410px" viewBox="0 0 120 120" fill="none" stroke="#111" stroke-width="4" stroke-linejoin="round">
    <circle cx="60" cy="18" r="10"/>
    <path d="M20 14 L42 44 H78 L100 14"/>
    <circle cx="60" cy="62" r="16"/><path d="M52 62 L58 68 L68 56"/>
    <path d="M44 76 L40 112 H52 L60 88 L68 112 H80 L76 76"/>
  </svg>
  <div class="abs pillar-label" style="left:822px">BODY</div>

  <div class="abs pillar-card" style="left:139px">Sed ut perspiciatis unde omnis<br>iste natus error sit voluptatem<br>iste natus error sit voluptatem</div>
  <div class="abs pillar-card" style="left:462px">Sed ut perspiciatis unde omnis<br>iste natus error sit voluptatem<br>iste natus error sit voluptatem</div>
  <div class="abs pillar-card" style="left:782px">Sed ut perspiciatis unde omnis<br>iste natus error sit voluptatem<br>iste natus error sit voluptatem</div>
</section>

<section>
  <div class="abs rules"></div>
  <h2 class="abs section-title" style="top:1998px">I DONT WANT TO DIE WITHOUT ANY SCARS</h2>

  <div class="abs rule-bar" style="top:2146px">Do not talk about OV</div>
  <div class="abs rule-disc" style="left:144px;top:2108px"></div>
  <div class="abs rule-tag" style="left:144px;top:2122px">RULE<br>01</div>

  <div class="abs rule-bar" style="top:2321px">Do not talk about OV</div>
  <div class="abs rule-disc" style="left:144px;top:2286px"></div>
  <div class="abs rule-tag" style="left:140px;top:2300px">RULE<br>02</div>

  <div class="abs rule-bar" style="top:2505px">Do not talk about OV</div>
  <div class="abs rule-disc" style="left:144px;top:2465px"></div>
  <div class="abs rule-tag" style="left:142px;top:2478px">RULE<br>03</div>

  <div class="abs rule-bar" style="top:2681px">Do not talk about OV</div>
  <div class="abs rule-disc" style="left:144px;top:2640px"></div>
  <div class="abs rule-tag" style="left:144px;top:2644px">RULE<br>04</div>

  <div class="abs rule-bar" style="top:2856px">Do not talk about OV</div>
  <div class="abs rule-disc" style="left:144px;top:2815px"></div>
  <div class="abs rule-tag" style="left:140px;top:2820px">RULE<br>05</div>

  <div class="abs rule-bar" style="top:3040px">Do not talk about OV</div>
  <div class="abs rule-disc" style="left:144px;top:2998px"></div>
  <div class="abs rule-tag" style="left:138px;top:3006px">RULE<br>06</div>

  <div class="abs rule-bar" style="top:3204px">Do not talk about OV</div>
  <div class="abs rule-disc" style="left:140px;top:3165px"></div>
  <div class="abs rule-tag" style="left:130px;top:3183px">RULE<br>07</div>

  <div class="abs rule-bar" style="top:3386px">Do not talk about OV</div>
  <div class="abs rule-disc" style="left:140px;top:3340px"></div>
  <div class="abs rule-tag" style="left:132px;top:3360px">RULE<br>08</div>
</section>

<section>
  <h2 class="abs section-title" style="top:3688px">I DONT WANT TO DIE WITHOUT ANY SCARS</h2>
  <div class="abs video" role="img" aria-label="Two boxers trading punches in a smoky dark ring"></div>
  <svg class="abs play" viewBox="0 0 60 60"><circle cx="30" cy="30" r="30" fill="#e01f3d"/><polygon points="23,17 44,30 23,43" fill="#fff"/></svg>
</section>

<section>
  <div class="abs faq"></div>
  <h2 class="abs section-title" style="top:4276px;left:-20px">COMMON QUESTIONS</h2>
  <div class="abs faq-frame"></div>
  <div class="abs faq-q" style="top:4386px">Why the “K7”?</div>
  <svg class="abs chev" style="left:874px;top:4412px" viewBox="0 0 22 12"><path d="M2 10 L11 3 L20 10" fill="none" stroke="#222" stroke-width="2"/></svg>
  <div class="abs faq-a">
    <ul>
      <li>“Sed ut perspiciatis unde omnis iste natus error sit voluptatesantium</li>
      <li>doloremque laudantium, totam rem aperiam, eaque ipsa quae ab illo</li>
      <li>inventore veritatis et quasi architecto beatae vitae dibo. ipsam</li>
      <li>luptatem quia</li>
    </ul>
  </div>
  <div class="abs faq-q" style="top:4615px">How dos someone get invites?</div>
  <svg class="abs chev" style="left:874px;top:4641px" viewBox="0 0 22 12"><path d="M2 3 L11 10 L20 3" fill="none" stroke="#222" stroke-width="2"/></svg>
</section>

<footer>
  <div class="abs footer"></div>
  <div class="abs social" style="left:534px"></div>
  <div class="abs social" style="left:572px"></div>
  <div class="abs social" style="left:610px"></div>
  <div class="abs social" style="left:648px"></div>
  <div class="abs foot-brand">VANTAGE</div>
  <span class="abs foot-link" style="left:276px">HOME</span>
  <span class="abs foot-link" style="left:366px">ABOUT US</span>
  <span class="abs foot-link" style="left:496px">SERVICES</span>
  <span class="abs foot-link" style="left:628px">TESTIMONIALS</span>
  <span class="abs foot-link" style="left:818px">CONTACT US</span>
  <div class="abs foot-rule"></div>
  <p class="abs copy">© 2023&nbsp; Vantage Com All Rights Reserved.</p>
</footer>

</body>
</html>
```